New website: Wanderfjordia.com

We need to build a website for our small travel agency.
We want to be able to upload our brochures and offer our tours on site. No online payments involved yet.

We want to create an exact copy of another website: www.trekvalora.is, but with our own information and products. We like that design very much.

We are not going to do any sales via the website as the website above, but instead we want to show in the same style and everything the different tours that we offer.

We need to be able to modify tours: tour pictures, info, add videos, text, etc.

We need the website in English and Spanish. We can provide the Spanish translation.

We would advice you to create a copy of that website, with the text to be editable by us.
We own the website www.wanderfjordia.com and need that the designer uploads it and makes it work as well.

We have uploaded some pictures that can be used as place markers.

I HAVE UPLOADED OUR BROCHURE DEMO SO YOU CAN GET MORE INFO IN ENGLISH ABOUT US AND MORE PICTURES.

PLEASE REMEMBER THAT THE WEBSITE ¨MOVES¨ when you resize it! Specially the pictures get ¨bigger¨ or smaller¨ when you resize. The same applies to the logos :-)

Once you have created the front page just as the original website I will select it and then we can put the real info and extra pages :-)

Tourists, international people traveling.

Tourism

Coded - Design and coding required

5+ page

Sans Serif

ffffff

• Exactly the same layout of the website mentioned (www.trekvalora.is)
• Everything the same, but with our own logo, texts and photos.
• HOME
• TOURS
• GROUPS
• OUR MOST POPULAR TOURS

```html
<!DOCTYPE html>
<html lang="es">
<head>
<meta charset="utf-8">
<title>Wanderfjordia</title>
<link href="https://fonts.googleapis.com/css2?family=Source+Sans+3:wght@300;400;600;700&display=swap" rel="stylesheet">
<style>
:root{
  --red:#e3262b;
  --ink:#1d1d1d;
  --text:#3a3a3a;
  --muted:#9a9a9a;
  --line:#d8d8d8;
  --white:#ffffff;
  --footer:#151515;
  --footer-text:#cfcfcf;
}
*{margin:0;padding:0;box-sizing:border-box}
html,body{width:1200px;height:3303px;overflow:hidden;background:var(--white)}
body{position:relative;font-family:"Source Sans 3",Arial,sans-serif;color:var(--text)}
.abs{position:absolute}

/* header */
.brand{left:165px;top:26px;width:112px;height:112px;border-radius:50%;background:#111;display:flex;align-items:center;justify-content:center;color:var(--white);font-weight:600;font-size:12px;letter-spacing:0;white-space:nowrap}
.lang{right:146px;top:34px;font-size:9px;letter-spacing:.5px;color:#555;display:flex;align-items:center;gap:6px}
.lang .flag{width:24px;height:15px;background:linear-gradient(#c9393d 0 50%,#e9e9ef 50% 100%)}
.nav{left:480px;top:86px;display:flex;font-size:19px;font-weight:300;color:#333}
.nav a{color:inherit;text-decoration:none;margin-right:38px;position:relative}
.nav a.active{color:var(--ink)}
.nav a.active::after{content:"";position:absolute;left:-6px;right:-6px;bottom:-17px;height:3px;background:var(--red)}
.nav-pin{left:494px;top:44px}

/* hero */
.hero-main{left:0;top:150px;width:600px;height:537px;background:linear-gradient(180deg,#9bb8d6 0%,#c7d3de 30%,#5d6770 55%,#39505c 78%,#2e3c44 100%)}
.hero-top{left:600px;top:150px;width:600px;height:267px;background:linear-gradient(180deg,#3f76b4 0%,#a9c2dc 40%,#6f7a86 70%,#3c4a58 100%)}
.hero-bottom{left:600px;top:420px;width:600px;height:267px;background:linear-gradient(180deg,#2d6fb6 0%,#9fc0de 45%,#7a8f97 65%,#416c86 100%)}
.hero-caption{position:absolute;left:0;bottom:30px;padding-left:34px}
.hero-main .hero-caption{left:112px;bottom:36px}
.hero-caption h2{color:var(--white);font-weight:600;font-size:27px;letter-spacing:1px}
.hero-caption p{color:#eee;font-size:12px;font-style:italic}
.hero-arrow{position:absolute;right:18px;bottom:20px;width:40px;height:40px;border-radius:50%;background:var(--white);display:flex;align-items:center;justify-content:center}
.hero-main .hero-arrow{right:22px}
.hero-pin{position:absolute}

/* section titles */
.section-title{font-weight:300;font-size:48px;color:var(--ink);letter-spacing:1px;display:flex;align-items:center;line-height:1;white-space:nowrap}
.section-title svg{margin:0 1px}

.tabs{left:186px;top:840px;display:flex;font-size:13px;color:#222;font-weight:600;white-space:nowrap}
.tabs span{margin-right:11px}
.tabs span.sep{color:#777;font-weight:400;margin-right:14px}
.tabs .active{position:relative}
.tabs .active::after{content:"";position:absolute;left:0;right:0;bottom:-11px;height:3px;background:var(--red)}

/* tour cards */
.tour{width:290px}
.tour .photo{width:290px;height:205px;border:6px solid #dcdcdc}
.tour h3{margin-top:40px;font-size:18px;font-weight:600;color:var(--ink)}
.tour .length{font-size:12px;color:var(--muted);margin-top:2px}
.tour .price{font-size:34px;font-weight:400;color:var(--red);line-height:1.1}

.btn{left:434px;top:1693px;width:315px;height:63px;border:3px solid var(--red);display:flex;align-items:center;justify-content:center;font-size:18px;font-weight:600;color:#222;letter-spacing:.3px}

.divider{left:150px;width:900px;height:30px;background:radial-gradient(ellipse at 50% 0%,rgba(0,0,0,.08),rgba(0,0,0,0) 70%)}

.about p{font-size:13px;line-height:24px;color:#333;width:500px}
.art{border-radius:6px}

/* footer */
.footer{left:0;top:2957px;width:1200px;height:346px;background:var(--footer);color:var(--footer-text)}
.footer .logo{position:absolute;left:143px;top:33px;width:121px;height:121px;border-radius:50%;border:3px solid var(--white);display:flex;align-items:center;justify-content:center;color:var(--white);font-weight:600;font-size:12px;white-space:nowrap}
.footer ul{position:absolute;list-style:none;font-size:13px;line-height:24px;white-space:nowrap}
.footer .copy{position:absolute;left:143px;top:296px;font-size:12px}
.footer .social{position:absolute;left:805px;top:296px;font-size:12px;display:flex;align-items:center;gap:9px}
.footer .social i{display:block;width:9px;height:9px;border-radius:50%;background:var(--red)}
.footer .lang-code{position:absolute;right:32px;top:296px;font-size:12px}
</style>
</head>
<body>

<header>
  <div class="abs brand">WANDERFJORDIA</div>
  <div class="abs lang">LANGUAGES <span class="flag" role="img" aria-label="English flag"></span>
    <svg width="8" height="6" viewBox="0 0 8 6"><path d="M1 1l3 3 3-3" fill="none" stroke="#777"/></svg></div>
  <svg class="abs nav-pin" width="22" height="30" viewBox="0 0 22 30" aria-hidden="true"><path d="M11 0C5 0 0 5 0 11c0 8 11 19 11 19s11-11 11-19C22 5 17 0 11 0z" fill="#111"/><circle cx="11" cy="11" r="5" fill="var(--red)"/></svg>
  <nav class="abs nav">
    <a class="active" href="#">HOME</a><a href="#">TOURS</a><a href="#">GROUPS</a><a href="#" style="margin-right:44px">RENT A CAR</a><a href="#" style="margin-right:36px">FLIGHT</a><a href="#">CONTACT</a>
  </nav>
</header>

<section>
  <div class="abs hero-main" role="img" aria-label="Granite peaks above a lake with hikers in Patagonia">
    <svg class="hero-pin" style="left:306px;top:150px" width="48" height="64" viewBox="0 0 22 30"><path d="M11 0C5 0 0 5 0 11c0 8 11 19 11 19s11-11 11-19C22 5 17 0 11 0z" fill="#111"/><circle cx="11" cy="11" r="6" fill="var(--red)"/></svg>
    <div class="hero-caption"><h2>PATAGONIA</h2><p>Neque porro quisquam est qui dolorem ipsum</p></div>
    <div class="hero-arrow"><svg width="20" height="20" viewBox="0 0 20 20"><path d="M3 10h13M10 4l6 6-6 6" fill="none" stroke="#111" stroke-width="3"/></svg></div>
  </div>
  <div class="abs hero-top" role="img" aria-label="Snowy mountain range under clouds">
    <svg class="hero-pin" style="left:214px;top:100px" width="48" height="64" viewBox="0 0 22 30"><path d="M11 0C5 0 0 5 0 11c0 8 11 19 11 19s11-11 11-19C22 5 17 0 11 0z" fill="#111"/><circle cx="11" cy="11" r="6" fill="var(--red)"/></svg>
    <div class="hero-caption"><h2>PATAGONIA</h2><p>Neque porro quisquam est qui dolorem ipsum</p></div>
    <div class="hero-arrow"><svg width="20" height="20" viewBox="0 0 20 20"><path d="M3 10h13M10 4l6 6-6 6" fill="none" stroke="#111" stroke-width="3"/></svg></div>
  </div>
  <div class="abs hero-bottom" role="img" aria-label="Mountain peaks over a blue lake">
    <svg class="hero-pin" style="left:282px;top:42px" width="48" height="64" viewBox="0 0 22 30"><path d="M11 0C5 0 0 5 0 11c0 8 11 19 11 19s11-11 11-19C22 5 17 0 11 0z" fill="#111"/><circle cx="11" cy="11" r="6" fill="var(--red)"/></svg>
    <div class="hero-caption"><h2>PATAGONIA</h2><p>Neque porro quisquam est qui dolorem ipsum</p></div>
    <div class="hero-arrow"><svg width="20" height="20" viewBox="0 0 20 20"><path d="M3 10h13M10 4l6 6-6 6" fill="none" stroke="#111" stroke-width="3"/></svg></div>
  </div>
</section>

<section>
  <h1 class="abs section-title" style="left:482px;top:730px">OUR T<svg width="32" height="44" viewBox="0 0 22 30"><path d="M11 0C5 0 0 5 0 11c0 8 11 19 11 19s11-11 11-19C22 5 17 0 11 0z" fill="#111"/><circle cx="11" cy="11" r="5" fill="var(--red)"/></svg>URS</h1>
  <div class="abs tabs">
    <span class="active">Popular Tours</span><span class="sep">|</span><span>Day Tours</span><span class="sep">|</span><span>Travel by Air Tours</span><span class="sep">|</span><span>Self Drive Tours</span><span class="sep">|</span><span>Adventures Tours</span><span class="sep">|</span><span>Customize Tours</span><span class="sep">|</span><span>Transfer</span>
  </div>

  <article class="abs tour" style="left:143px;top:940px"><div class="photo" role="img" aria-label="Jagged peaks and road in Patagonia" style="background:linear-gradient(180deg,#2d63b5,#9cb8d6 50%,#4d5a4c 75%,#8a7a5a)"></div><h3>Patagonia</h3><p class="length">length: 7 hours</p><p class="price">8,800 ISK</p></article>
  <article class="abs tour" style="left:455px;top:940px"><div class="photo" role="img" aria-label="Dark peaks above a glacial lake" style="background:linear-gradient(180deg,#7e8a96,#c9ccd0 40%,#4a4f4a 70%,#3f7f8a)"></div><h3>Patagonia</h3><p class="length">length: 7 hours</p><p class="price">8,800 ISK</p></article>
  <article class="abs tour" style="left:766px;top:940px"><div class="photo" role="img" aria-label="Hiker facing snowy mountains" style="background:linear-gradient(180deg,#4a7fb8,#dfe8f0 45%,#7f98ad 75%,#5c6d7c)"></div><h3>Patagonia</h3><p class="length">length: 7 hours</p><p class="price">8,800 ISK</p></article>

  <article class="abs tour" style="left:143px;top:1306px"><div class="photo" role="img" aria-label="Mountains over golden plains" style="background:linear-gradient(180deg,#8aa2bf,#d7dde3 40%,#626a70 65%,#8b7a4f)"></div><h3>Patagonia</h3><p class="length">length: 7 hours</p><p class="price">8,800 ISK</p></article>
  <article class="abs tour" style="left:455px;top:1306px"><div class="photo" role="img" aria-label="Granite spires over a rocky valley" style="background:linear-gradient(180deg,#1f5fb0,#b8cde2 45%,#6d6f70 70%,#8e8f8c)"></div><h3>Patagonia</h3><p class="length">length: 7 hours</p><p class="price">8,800 ISK</p></article>
  <article class="abs tour" style="left:766px;top:1306px"><div class="photo" role="img" aria-label="Mountains reflected in a lake at dusk" style="background:linear-gradient(180deg,#24468a,#8fa6c8 45%,#3c5a84 65%,#1f3a66)"></div><h3>Patagonia</h3><p class="length">length: 7 hours</p><p class="price">8,800 ISK</p></article>

  <a class="abs btn">VIEW ALL OUR POPULAR TOURS</a>
  <div class="abs divider" style="top:1800px"></div>
</section>

<section class="about">
  <h2 class="abs section-title" style="left:141px;top:1896px">QUIENES S<svg width="32" height="44" viewBox="0 0 22 30"><path d="M11 0C5 0 0 5 0 11c0 8 11 19 11 19s11-11 11-19C22 5 17 0 11 0z" fill="#111"/><circle cx="11" cy="11" r="5" fill="var(--red)"/></svg>MOS</h2>
  <p class="abs" style="left:143px;top:1984px">Somos una empresa conformada por un idóneo equipo de trabajo que consta de alta motivación, óptimo entrenamiento, elevado capital humano y cuyos integrantes poseen más de 10 años de experiencia trabajando en forma independiente en Turismo Receptivo Regional, Nacional e Internacional. En conjunto nos potenciamos y logramos satisfacer las altas demandas de servicios turísticos requeridos por nuestros clientes.</p>
  <div class="abs art" role="img" aria-label="Folded travel map with two red flags" style="left:672px;top:1900px;width:385px;height:200px;background:linear-gradient(180deg,#f2ecd8,#e3dcbf)"></div>

  <div class="abs art" role="img" aria-label="Pile of travel landmarks on a suitcase" style="left:160px;top:2180px;width:300px;height:350px;background:linear-gradient(180deg,#e9e0d2,#c9a57a)"></div>
  <h2 class="abs section-title" style="left:532px;top:2257px">MISI<svg width="32" height="44" viewBox="0 0 22 30"><path d="M11 0C5 0 0 5 0 11c0 8 11 19 11 19s11-11 11-19C22 5 17 0 11 0z" fill="#111"/><circle cx="11" cy="11" r="5" fill="var(--red)"/></svg>N</h2>
  <p class="abs" style="left:534px;top:2338px">Somos una empresa conformada por un idóneo equipo de trabajo que consta de alta motivación, óptimo entrenamiento, elevado capital humano y cuyos integrantes poseen más de 10 años de experiencia trabajando en forma independiente en Turismo Receptivo Regional, Nacional e Internacional. En conjunto nos potenciamos y logramos satisfacer las altas demandas de servicios turísticos requeridos por nuestros clientes.</p>

  <h2 class="abs section-title" style="left:141px;top:2623px">VISI<svg width="32" height="44" viewBox="0 0 22 30"><path d="M11 0C5 0 0 5 0 11c0 8 11 19 11 19s11-11 11-19C22 5 17 0 11 0z" fill="#111"/><circle cx="11" cy="11" r="5" fill="var(--red)"/></svg>N</h2>
  <p class="abs" style="left:143px;top:2706px">Somos una empresa conformada por un idóneo equipo de trabajo que consta de alta motivación, óptimo entrenamiento, elevado capital humano y cuyos integrantes poseen más de 10 años de experiencia trabajando en forma independiente en Turismo Receptivo Regional, Nacional e Internacional. En conjunto nos potenciamos y logramos satisfacer las altas demandas de servicios turísticos requeridos por nuestros clientes.</p>
  <div class="abs art" role="img" aria-label="Stacked suitcases with a bon voyage sign" style="left:690px;top:2610px;width:280px;height:300px;background:linear-gradient(180deg,#f3e2c4,#e89a3c)"></div>
</section>

<footer class="abs footer">
  <div class="logo">WANDERFJORDIA</div>
  <ul style="left:374px;top:52px"><li>Home</li><li>Tours</li><li>Groups</li><li>Rent a Car</li><li>Flight</li><li>Contact</li></ul>
  <ul style="left:535px;top:52px"><li>Terms &amp; conditions</li><li>Privacy policy</li></ul>
  <ul style="left:768px;top:52px"><li>Nordlicht Reisewerk</li><li>Lindenweg 42b</li><li>10117 Berlin &nbsp;|&nbsp; Germany</li><li>&nbsp;</li><li>Telephone: +49 30 5550 1842</li><li>E-mail: hola@nordlichtreisewerk.de</li></ul>
  <p class="copy">© 2016 Company Name | All Rights Reserved</p>
  <div class="social">Connect With Us &nbsp;<i></i><i></i><i></i><i></i><i></i><i></i></div>
  <p class="lang-code">cs</p>
</footer>

</body>
</html>
```